KRL Stationery Design Project

Dear Designers,
We need a new stationery design for company to match our new logo.
Designers should provide a design for the following:
1. Business Card: 3.5x2 Inches.
2. Letterhead: A4 size.
3. Envelops: 25x35.5 Cm.
You can keep the Arabic name at the bottom of the logo Or you can use the separate attached Arabic Name.
Please refer to the attached logo guide for design information.
Sample Business Card information:
Name: Tarek Sowan
Position: Operation Manager
Tel: +966 920007164 Ex. 500
Fax: +966 (3)8842617
Mob: +966 (5)00263817
email: tarek@krl-example.com.sa
URL: www.krl-example.com.sa
Address:
Nakheel Heights, Suite 718
Zayed bin Omar Str.
Khobar, 31847
Saudi Arabia
Updates
Dear All,
Please note, we had uploaded our logo along with Arabic writing in Adobe illustrator format (.ai).
Regards,
Karim
Dear All,
A sample data for the business card had been added as per your request.
Regards,
Karim

```html
<!DOCTYPE html>
<html lang="en">
<head>
<meta charset="utf-8">
<title>KRL Business Card</title>
<link rel="stylesheet" href="https://fonts.googleapis.com/css2?family=Source+Sans+3:wght@400;600;700&display=swap">
<style>
  :root {
    --stage: #262626;
    --card: #ffffff;
    --navy: #0f2e50;
    --ink: #3c3c3c;
    --rule: #c9c9c9;
    --band-text: #ffffff;
  }
  * { margin: 0; padding: 0; box-sizing: border-box; }
  html, body {
    width: 960px; height: 1200px; overflow: hidden;
    background: var(--stage);
    font-family: "Source Sans 3", Arial, sans-serif;
  }
  .canvas { position: relative; width: 960px; height: 1200px; }
  .card {
    position: absolute; left: 60px; width: 840px; height: 479px;
    background: var(--card); border-radius: 30px; overflow: hidden;
  }
  .card--front { top: 88px; }
  .card--back { top: 643px; }

  .brand {
    position: absolute; display: flex; align-items: center; gap: 18px;
    color: var(--navy); font-weight: 700; letter-spacing: 2px;
  }
  .brand__mark { background: var(--navy); border-radius: 50%; flex: none; }
  .card--front .brand { left: 95px; top: 175px; font-size: 96px; line-height: 1; }
  .card--front .brand__mark { width: 52px; height: 52px; }
  .card--back .brand { left: 0; right: 0; justify-content: center; top: 175px; font-size: 120px; line-height: 1; }
  .card--back .brand__mark { width: 64px; height: 64px; }

  .divider {
    position: absolute; left: 487px; top: 134px; width: 3px; height: 186px;
    background: linear-gradient(to bottom, transparent, var(--rule) 20%, var(--rule) 80%, transparent);
  }
  .person { position: absolute; left: 523px; top: 142px; color: var(--ink); }
  .person__name { font-size: 27px; font-weight: 400; line-height: 1.1; }
  .person__role { font-size: 20px; margin-top: 4px; }
  .contact { list-style: none; margin-top: 14px; }
  .contact li { display: flex; align-items: center; gap: 10px; font-size: 20px; line-height: 28.5px; }
  .contact svg { width: 14px; height: 14px; fill: var(--ink); flex: none; }

  .address-band {
    position: absolute; left: 0; right: 0; bottom: 0; height: 62px;
    background: var(--navy); color: var(--band-text);
    display: flex; align-items: center; justify-content: center;
    font-size: 20px; letter-spacing: 0.2px;
  }
</style>
</head>
<body>
<main class="canvas">
  <section class="card card--front" aria-label="Business card front">
    <div class="brand"><span class="brand__mark"></span>KRL</div>
    <div class="divider"></div>
    <div class="person">
      <p class="person__name">Your Name</p>
      <p class="person__role">Designation</p>
      <ul class="contact">
        <li><svg viewBox="0 0 14 14" aria-hidden="true"><path d="M1 5c0-2 2-3 6-3s6 1 6 3v1h-3V5H4v1H1zM3 7h8l1 5H2z"/></svg>123-123-1234</li>
        <li><svg viewBox="0 0 14 14" aria-hidden="true"><path d="M3 1h8v4H3zM1 6h12v5h-2v2H3v-2H1zM4 9v3h6V9z"/></svg>123-123-1234</li>
        <li><svg viewBox="0 0 14 14" aria-hidden="true"><path d="M7 1a6 6 0 1 0 3 11l-.6-1.2A4.7 4.7 0 1 1 11.7 7v.6c0 .8-.5 1.2-1 1.2s-.9-.4-.9-1.2V4.2H8.6v.6A3 3 0 1 0 9 9.3c.4.6 1 .9 1.7.9 1.3 0 2.3-1 2.3-2.6V7A6 6 0 0 0 7 1zm0 7.8a1.8 1.8 0 1 1 0-3.6 1.8 1.8 0 0 1 0 3.6z"/></svg>info@krl-example.com.sa</li>
        <li><svg viewBox="0 0 14 14" aria-hidden="true"><circle cx="7" cy="7" r="6"/></svg>www.krl-example.com.sa</li>
      </ul>
    </div>
    <div class="address-band">1234, Suite# 123, Street Name, State NAME, Country Code</div>
  </section>

  <section class="card card--back" aria-label="Business card back">
    <div class="brand"><span class="brand__mark"></span>KRL</div>
  </section>
</main>
</body>
</html>
```